"Vine Hollow Excursions" is a top notch Santa Barbara County Wine Tour company.

We provide scenic, boutique and custom wine tours. I need the card to be clean and classy. I will provide our logo. I would like the logo to cover the back side of the card as an option and would like to see a couple color options other then our signature green and gold. I would like to see some creative options and let the designers come up with options.
I need cards for myself and my team. The final design should communicate "An authentic and boutique wine tour experience"
Please use my website for reference www.vinehollowexcursions.example

Target Market(s)

We have a wide range of clients from millennials to baby boomers

Industry/Entity Type

Tour

Contact Information for Business Card

Contact info:
Dale Morton
805-219-6384
info@vinehollowexcursions.example
vinehollowexcursions.example

Colors

Designer to choose colors to be used in the design.

Requirements
Must have
• my logo
Nice to have
• *I would like to have the backside side with the logo and the company statement
• "An authentic and boutique wine tour experience" as an option.
• *I would also like to see what the designers can create!
• *I would like to see an option that incorporates or social: instagram, yelp, trip advisor
Should not have
• I do not want it too busy.

```html
<!DOCTYPE html>
<html lang="en">
<head>
<meta charset="utf-8">
<title>Vine Hollow Excursions – Business Card</title>
<link rel="stylesheet" href="https://fonts.googleapis.com/css2?family=Roboto+Condensed:wght@400;700&family=Roboto:wght@300;400&display=swap">
<style>
  :root {
    --canvas-bg: #ece8e2;
    --card-white: #f6f6f4;
    --brand-green: #0b5d30;
    --brand-green-deep: #07502a;
    --gold-light: #c9b48c;
    --gold-dark: #8a7148;
    --text-grey: #4a4a4a;
    --social-brown: #8b6a4a;
    --social-green: #3e9a2e;
    --social-red: #d5231c;
  }
  * { margin: 0; padding: 0; box-sizing: border-box; }
  html, body {
    width: 1200px; height: 800px; overflow: hidden;
    background: var(--canvas-bg);
  }
  .canvas {
    width: 1200px; height: 800px;
    display: flex; align-items: center; justify-content: center; gap: 40px;
  }
  .card {
    width: 540px; height: 309px; position: relative; overflow: hidden;
    box-shadow: 0 10px 28px rgba(0,0,0,.18);
  }

  /* Front */
  .card-front { background: var(--card-white); }
  .edge-stripe { position: absolute; left: 0; top: 0; width: 24px; height: 100%; }
  .edge-stripe .gold { height: 54%; background: linear-gradient(180deg, var(--gold-light), var(--gold-dark)); }
  .edge-stripe .green { height: 46%; background: var(--brand-green); }
  .social-row { position: absolute; top: 26px; right: 30px; display: flex; gap: 7px; }
  .social-badge { width: 24px; height: 24px; border-radius: 5px; }
  .social-badge.one { background: var(--social-brown); }
  .social-badge.two { background: var(--social-green); }
  .social-badge.three { background: var(--social-red); }
  .brand-lockup {
    position: absolute; left: 62px; top: 70px;
    display: flex; align-items: center; gap: 12px;
  }
  .brand-mark { width: 30px; height: 30px; background: var(--brand-green); }
  .brand-name {
    font-family: "Roboto", sans-serif; font-weight: 400; font-size: 26px;
    color: var(--gold-dark); letter-spacing: .02em;
  }
  .contact { position: absolute; left: 62px; top: 168px; }
  .contact-name {
    font-family: "Roboto Condensed", sans-serif; font-weight: 700;
    font-size: 24px; color: var(--brand-green); text-transform: uppercase;
    margin-bottom: 8px;
  }
  .contact-line {
    font-family: "Roboto Condensed", sans-serif; font-size: 14px;
    color: var(--text-grey); text-transform: uppercase; line-height: 1.45;
  }
  .contact-line .label { font-weight: 700; color: var(--brand-green); margin-right: 4px; }

  /* Back */
  .card-back {
    background: var(--brand-green);
    display: flex; flex-direction: column; align-items: center; justify-content: center;
  }
  .back-name {
    font-family: "Roboto", sans-serif; font-weight: 400; font-size: 34px;
    color: #ffffff; letter-spacing: .03em; margin-bottom: 34px;
  }
  .statement {
    font-family: "Roboto", sans-serif; font-weight: 300; font-size: 16px;
    color: #eef3ee;
  }
</style>
</head>
<body>
<main class="canvas">
  <section class="card card-front" aria-label="Card front">
    <div class="edge-stripe"><div class="gold"></div><div class="green"></div></div>
    <div class="social-row">
      <span class="social-badge one"></span>
      <span class="social-badge two"></span>
      <span class="social-badge three"></span>
    </div>
    <div class="brand-lockup">
      <span class="brand-mark"></span>
      <span class="brand-name">Vine Hollow Excursions</span>
    </div>
    <div class="contact">
      <p class="contact-name">Dale Morton</p>
      <p class="contact-line"><span class="label">Phone:</span>805-219-6384</p>
      <p class="contact-line"><span class="label">Email:</span>info@vinehollowexcursions.example</p>
      <p class="contact-line"><span class="label">Web:</span>vinehollowexcursions.example</p>
    </div>
  </section>

  <section class="card card-back" aria-label="Card back">
    <p class="back-name">Vine Hollow Excursions</p>
    <p class="statement">An authentic &amp; boutique wine tour experience</p>
  </section>
</main>
</body>
</html>
```